New Grinvale Poster

This is for designer Doreen ONLY.<br/><br/>hi doreen,<br/><br/>Hope you are well.<br/>I need to redo my Grinvale combo. <br/>So the layout I want is clean and simple. <br/>Photo is on the left hand side, then combo's details and price.<br/>Same poster size.<br/>Thank you<br/><br/><br/>Pho Combo: 1x Pho + 1x Side + 1x Drinks = $23<br/>Noodle Salad Combo: 1x Noodle Salads + 1x Side + 1x Drinks = $23<br/>Rice Combo: 1x Rice + 1x Side + 1x Drinks = $25<br/>Combo for 2: 2x mains + 1x side + 2x Drinks = $39<br/>Family Combo: 4x mains + 2 sides + 4x Drinks = 79

```html
<!DOCTYPE html>
<html lang="en">
<head>
<meta charset="utf-8">
<title>Grinvale Combo Poster</title>
<link href="https://fonts.googleapis.com/css2?family=Open+Sans:wght@600;700;800&display=swap" rel="stylesheet">
<style>
  :root {
    --backdrop: #5f7273;
    --poster: #3a3a3b;
    --poster-deep: #323233;
    --photo-dark: #1e2429;
    --photo-mid: #2b3238;
    --accent: #f7941d;
    --line: #c9761c;
    --white: #ffffff;
  }
  * { margin: 0; padding: 0; box-sizing: border-box; }
  html, body {
    width: 1200px; height: 1200px; overflow: hidden;
    background: var(--backdrop);
    font-family: "Open Sans", Arial, sans-serif;
  }
  .poster {
    position: absolute; left: 208px; top: 46px;
    width: 784px; height: 1107px;
    background: radial-gradient(ellipse at 40% 30%, var(--poster) 0%, var(--poster-deep) 100%);
    color: var(--white);
  }
  .headline {
    position: absolute; left: 72px; top: 58px;
    font-weight: 800; line-height: 1; letter-spacing: -1px;
  }
  .headline .big { display: block; font-size: 92px; line-height: 80px; }
  .headline .small { display: block; font-size: 50px; line-height: 56px; margin-top: 4px; }
  .brand {
    position: absolute; left: 576px; top: 72px;
    width: 140px; height: 140px;
    border: 2px solid var(--white); border-radius: 50%;
    display: flex; align-items: center; justify-content: center;
    text-align: center;
    font-weight: 700; font-size: 17px; line-height: 1.2; color: var(--accent);
  }
  .photos {
    position: absolute; left: 70px; top: 291px; width: 296px; height: 753px;
    display: flex; flex-direction: column; gap: 2px;
  }
  .photo {
    flex: 1;
    background: radial-gradient(ellipse at 55% 50%, var(--photo-mid) 0%, var(--photo-dark) 100%);
  }
  .combo {
    position: absolute; left: 366px; width: 367px; height: 120px;
    border: 1px solid var(--line); border-left: none;
  }
  .combo-name {
    position: absolute; left: 22px; top: 14px;
    font-weight: 800; font-size: 26px; line-height: 30px; white-space: nowrap;
  }
  .combo-items {
    position: absolute; left: 22px; top: 45px;
    font-weight: 600; font-size: 15.5px; white-space: nowrap;
  }
  .combo-items b { font-weight: 800; }
  .price {
    position: absolute; left: 19px; top: 66px;
    width: 62px; height: 62px; border-radius: 50%;
    background: var(--accent);
    display: flex; align-items: center; justify-content: center;
    font-weight: 800; font-size: 28px; letter-spacing: -0.5px;
  }
</style>
</head>
<body>
<main class="poster">
  <h1 class="headline">
    <span class="big">GRIN-</span>
    <span class="big">VALE</span>
    <span class="small">COMBO</span>
  </h1>

  <div class="brand">BOWL &amp; DASH</div>

  <div class="photos">
    <div class="photo" role="img" aria-label="Pho bowl with a side plate and a bottled drink"></div>
    <div class="photo" role="img" aria-label="Noodle salad with rice paper rolls and a bottled drink"></div>
    <div class="photo" role="img" aria-label="Rice dish with spring rolls and a bottled drink"></div>
    <div class="photo" role="img" aria-label="Two main dishes with spring rolls and two drinks"></div>
    <div class="photo" role="img" aria-label="Four main dishes, two sides and four drinks"></div>
  </div>

  <section class="combo" style="top:308px">
    <h2 class="combo-name">PHỞ COMBO</h2>
    <p class="combo-items"><b>1x</b> PHỞ + <b>1x</b> SIDE + <b>1x</b> DRINKS</p>
    <div class="price">$23</div>
  </section>

  <section class="combo" style="top:462px">
    <h2 class="combo-name">NOODLE SALAD COMBO</h2>
    <p class="combo-items"><b>1x</b> NOODLE SALAD + <b>1x</b> SIDE + <b>1x</b> DRINKS</p>
    <div class="price">$23</div>
  </section>

  <section class="combo" style="top:611px">
    <h2 class="combo-name">RICE COMBO</h2>
    <p class="combo-items"><b>1x</b> RICE + <b>1x</b> SIDE + <b>1x</b> DRINKS</p>
    <div class="price">$25</div>
  </section>

  <section class="combo" style="top:762px">
    <h2 class="combo-name">COMBO FOR 2</h2>
    <p class="combo-items"><b>2x</b> MAINS + <b>1x</b> SIDE + <b>2x</b> DRINKS</p>
    <div class="price">$39</div>
  </section>

  <section class="combo" style="top:911px">
    <h2 class="combo-name">FAMILY COMBO</h2>
    <p class="combo-items"><b>4x</b> MAINS + <b>2x</b> SIDES + <b>4x</b> DRINKS</p>
    <div class="price">$79</div>
  </section>
</main>
</body>
</html>
```